Oil and Gas Exploration and Production company needs a business card design

We need a business card design using our logo and colors in the logo. We want a mainstream design.

```html
<!DOCTYPE html>
<html lang="en">
<head>
<meta charset="utf-8">
<title>Corvan Oil &amp; Gas — Business Card</title>
<link rel="stylesheet" href="https://fonts.googleapis.com/css2?family=Crimson+Text:wght@400;700&display=swap">
<style>
  :root {
    --card-bg: #f3f3f3;
    --ink: #1f1f1f;
    --charcoal: #333333;
    --gold: #c99a33;
    --white: #ffffff;
  }
  * { margin: 0; padding: 0; box-sizing: border-box; }
  html, body { width: 1200px; height: 720px; overflow: hidden; background: var(--card-bg); }
  .card {
    position: relative;
    width: 1200px;
    height: 720px;
    background: var(--card-bg);
    font-family: "Crimson Text", Georgia, serif;
    color: var(--ink);
    overflow: hidden;
  }

  /* Brand name block */
  .brand {
    position: absolute;
    left: 0; right: 0; top: 78px;
    display: flex;
    justify-content: center;
    align-items: center;
    gap: 22px;
  }
  .brand-dot {
    width: 74px; height: 74px;
    border-radius: 50%;
    background: var(--gold);
    flex: none;
  }
  .brand-name {
    font-weight: 700;
    color: var(--ink);
    line-height: 1;
    text-align: left;
  }
  .brand-name .primary { display: block; font-size: 118px; letter-spacing: 1px; }
  .brand-name .secondary { display: block; font-size: 46px; letter-spacing: 9px; margin-top: 6px; }

  /* Contact icon tab */
  .icon-tab {
    position: absolute;
    left: 0; top: 399px;
    width: 84px; height: 222px;
    background: var(--gold);
    border-radius: 0 22px 22px 0;
  }
  .icon-tab svg { position: absolute; left: 26px; width: 28px; height: 28px; fill: var(--white); }

  .contact-list { position: absolute; left: 110px; top: 420px; list-style: none; }
  .contact-list li { font-size: 26px; height: 53px; line-height: 34px; }

  /* Person block */
  .person {
    position: absolute;
    right: 91px; top: 424px;
    text-align: right;
  }
  .person-name { font-size: 29px; font-weight: 700; color: var(--gold); line-height: 38px; }
  .person-title { font-size: 24px; line-height: 32px; }
  .person-address { margin-top: 30px; font-size: 25px; font-weight: 700; color: var(--gold); line-height: 39px; }
  .accent-rule {
    position: absolute;
    left: 1139px; top: 425px;
    width: 7px; height: 175px;
    background: var(--charcoal);
  }

  .footer-bands { position: absolute; left: 0; bottom: 0; width: 1200px; height: 40px; }
</style>
</head>
<body>
<main class="card">

  <header class="brand">
    <span class="brand-dot" aria-hidden="true"></span>
    <h1 class="brand-name">
      <span class="primary">Corvan</span>
      <span class="secondary">OIL &amp; GAS</span>
    </h1>
  </header>

  <div class="icon-tab" aria-hidden="true">
    <!-- desk phone -->
    <svg viewBox="0 0 24 24" style="top:16px">
      <path d="M2 8c0-3 4-5 10-5s10 2 10 5v2h-5V8c0-1-2-1.5-5-1.5S7 7 7 8v2H2z"/>
      <path d="M6 12h12l3 8H3z"/>
    </svg>
    <!-- handset -->
    <svg viewBox="0 0 24 24" style="top:65px">
      <path d="M6.6 2.5l3 3.2-1.8 2.6c1.3 3 3.6 5.3 6.6 6.6l2.6-1.8 3.2 3-2.2 3.4C10.6 19 4.9 13.4 3.2 4.7z"/>
    </svg>
    <!-- printer -->
    <svg viewBox="0 0 24 24" style="top:118px">
      <path d="M6 2h12v5H6z"/>
      <path d="M2 8h20v9h-4v-3H6v3H2z"/>
      <path d="M7 15h10v7H7z"/>
    </svg>
    <!-- envelope -->
    <svg viewBox="0 0 24 24" style="top:174px">
      <path d="M1 4h22v16H1zM3 6v.6l9 7 9-7V6zm0 3.2V18h18V9.2l-9 7z" fill-rule="evenodd"/>
    </svg>
  </div>

  <ul class="contact-list">
    <li>555.010.4821</li>
    <li>555.010.7364</li>
    <li>555.010.2957</li>
    <li>dwhitfield@corvanenergy.com</li>
  </ul>

  <section class="person">
    <p class="person-name">Dana Whitfield</p>
    <p class="person-title">Chief Executive Offer</p>
    <address class="person-address" style="font-style:normal">
      4150 Harlow Pkwy, Suite 210<br>
      Millbrook, NC 27000
    </address>
  </section>
  <span class="accent-rule" aria-hidden="true"></span>

  <svg class="footer-bands" viewBox="0 0 1200 40" aria-hidden="true">
    <rect x="0" y="10" width="760" height="30" fill="var(--charcoal)"/>
    <path d="M706 40 Q712 2 770 0 H1200 V40 Z" fill="var(--white)"/>
    <path d="M720 40 Q728 6 776 6 H1200 V40 Z" fill="var(--gold)"/>
  </svg>

</main>
</body>
</html>
```